TalkHarbor - Language Coaching Services

Sleek, innovative, trendy design for Language Coaching business.

TalkHarbor is a new UK based company that provides Language Coaching services. We offer highly personalized on-line and face to face language courses. We also impart learning techniques workshops based on the latest neuroscience research for second-language acquisition.

Target Market(s)

See attached info

Industry/Entity Type

Consulting

Contact Information for Business Card

TalkHarbor
DaniaKV@talkharbor.co.uk
TalkHarbor.co.uk
London, UK

Font styles to use
Sans Serif

```html
<!DOCTYPE html>
<html lang="en">
<head>
<meta charset="utf-8">
<title>TalkHarbor Business Card</title>
<link href="https://fonts.googleapis.com/css2?family=Roboto:wght@400;500;700&display=swap" rel="stylesheet">
<style>
  :root {
    --page-bg: #e7e7e7;
    --card-white: #ffffff;
    --brand-blue: #1a93cf;
    --name-blue: #1f7fb8;
    --text-grey: #5c5c5c;
    --title-grey: #9a9a9a;
    --divider: #d4d4d4;
    --back-light: #12b3ea;
    --back-mid: #0590c8;
    --back-dark: #035a8c;
  }
  * { margin: 0; padding: 0; box-sizing: border-box; }
  html, body {
    width: 1125px; height: 1200px; overflow: hidden;
    background: var(--page-bg);
    font-family: "Roboto", Arial, sans-serif;
  }
  .card {
    position: absolute; left: 150px; width: 825px; height: 471px;
    border-radius: 24px; overflow: hidden;
  }
  .card--front { top: 98px; background: var(--card-white); }
  .card--back {
    top: 631px;
    background: radial-gradient(ellipse 60% 70% at 50% 45%, var(--back-light) 0%, var(--back-mid) 50%, var(--back-dark) 100%);
  }
  .brand-block {
    position: absolute; left: 86px; top: 150px; width: 310px;
    display: flex; flex-direction: column; align-items: center;
  }
  .brand-circle {
    width: 118px; height: 118px; border-radius: 50%;
    border: 10px solid var(--brand-blue);
  }
  .brand-name {
    margin-top: 8px;
    font-size: 44px; font-weight: 500; color: var(--brand-blue);
    letter-spacing: 0.5px; line-height: 1;
  }
  .divider {
    position: absolute; left: 424px; top: 137px; width: 1px; height: 207px;
    background: var(--divider);
  }
  .contact { position: absolute; left: 464px; top: 138px; }
  .contact__name {
    font-size: 30px; font-weight: 700; color: var(--name-blue); line-height: 1.1;
  }
  .contact__title {
    font-size: 20px; font-weight: 500; color: var(--title-grey); line-height: 1.2; margin-top: 2px;
  }
  .contact__city {
    font-size: 19px; color: var(--text-grey); margin-top: 16px; line-height: 1.2;
  }
  .contact__list { list-style: none; margin-top: 13px; }
  .contact__item {
    display: flex; align-items: center; gap: 11px;
    font-size: 19px; color: var(--text-grey); height: 27px;
  }
  .contact__icon { width: 19px; height: 19px; flex: none; }
  .back-mark {
    position: absolute; left: 280px; top: 90px; width: 264px; height: 264px;
    border-radius: 50%; border: 16px solid var(--card-white);
    display: flex; align-items: center; justify-content: center;
  }
  .back-mark__name {
    font-size: 36px; font-weight: 500; color: var(--card-white);
  }
  .back-url {
    position: absolute; left: 0; right: 0; top: 400px; text-align: center;
    font-size: 20px; color: var(--card-white); letter-spacing: 6px;
  }
</style>
</head>
<body>
  <section class="card card--front">
    <div class="brand-block">
      <div class="brand-circle"></div>
      <div class="brand-name">TalkHarbor</div>
    </div>
    <div class="divider"></div>
    <div class="contact">
      <div class="contact__name">OWEN HARTLEY</div>
      <div class="contact__title">CEO/FOUNDER</div>
      <div class="contact__city">London, UK</div>
      <ul class="contact__list">
        <li class="contact__item">
          <svg class="contact__icon" viewBox="0 0 20 20"><rect x="5" y="1" width="10" height="18" rx="2" fill="none" stroke="#1f7fb8" stroke-width="2"/><rect x="7" y="3.5" width="6" height="11" fill="#1f7fb8"/></svg>
          689 512 0473
        </li>
        <li class="contact__item">
          <svg class="contact__icon" viewBox="0 0 20 20"><rect x="1" y="4" width="18" height="12" fill="#1f7fb8"/><path d="M1 4l9 7 9-7" fill="none" stroke="#fff" stroke-width="1.6"/></svg>
          DaniaKV@talkharbor.co.uk
        </li>
        <li class="contact__item">
          <svg class="contact__icon" viewBox="0 0 20 20"><circle cx="10" cy="10" r="9" fill="#1f7fb8"/><path d="M5 6c2 0 3 2 2 4s1 3 1 5M12 3c0 2 3 2 2 5s2 2 3 3" fill="none" stroke="#fff" stroke-width="1.6"/></svg>
          TalkHarbor.co.uk
        </li>
      </ul>
    </div>
  </section>

  <section class="card card--back">
    <div class="back-mark"><span class="back-mark__name">TalkHarbor</span></div>
    <div class="back-url">www.TalkHarbor.co.uk</div>
  </section>
</body>
</html>
```